I would like a business card to match my truck wrap and logo. I would like the font to match my existing business card please.

Industry/Entity Type

Painter

Contact Information for Business Card

Rodrigo Fenwar 801-437-2190 Fenwarcoatings.utah@brelmox.com
SERVICES - Custom Paint & Stain, Interior & Exterior, Epoxy Coatings / Garage Floors, Cabinet Refinishing, Log Staining and Refinishing.

Requirements
Nice to have
• I would like to have the white and grey line like the bottom of my vehicle wrap, Light Grey to match my truck also.

```html
<!DOCTYPE html>
<html lang="en">
<head>
<meta charset="utf-8">
<title>Fenwar Coatings – Business Card</title>
<link rel="stylesheet" href="https://fonts.googleapis.com/css2?family=Michroma&display=swap">
<style>
  :root {
    --stage: #1f2022;
    --card: #f1f1f0;
    --card-white: #f7f7f6;
    --band-grey: #b9b9b9;
    --line-grey: #cfcfcf;
    --line-white: #f4f4f4;
    --navy: #0d4a9c;
    --blue: #1266c4;
    --sky: #1a9be0;
  }
  * { box-sizing: border-box; margin: 0; padding: 0; }
  html, body { width: 1200px; height: 788px; overflow: hidden; }
  body {
    background: var(--stage);
    font-family: "Michroma", sans-serif;
    display: flex;
    align-items: center;
    justify-content: center;
    gap: 40px;
  }
  .card {
    position: relative;
    width: 540px;
    height: 309px;
    overflow: hidden;
    box-shadow: 0 14px 30px rgba(0,0,0,.45);
  }
  .card--front { background: var(--card); }
  .card--back { background: var(--card-white); }

  .card__stripes { position: absolute; inset: 0; }

  .front__email {
    position: absolute;
    top: 14px;
    left: 22px;
    font-size: 9.5px;
    color: var(--blue);
    letter-spacing: .2px;
  }
  .front__identity {
    position: absolute;
    left: 40px;
    top: 118px;
  }
  .front__name {
    font-size: 33px;
    line-height: 1;
    color: var(--blue);
    letter-spacing: 1px;
    text-transform: uppercase;
    font-weight: 400;
  }
  .front__phone {
    margin-top: 6px;
    margin-left: 38px;
    font-size: 21px;
    color: var(--navy);
    letter-spacing: .5px;
  }
  .brand {
    position: absolute;
    display: flex;
    align-items: center;
    gap: 12px;
  }
  .brand__mark {
    width: 40px;
    height: 40px;
    background: var(--blue);
  }
  .brand__name {
    font-size: 17px;
    line-height: 1.15;
    color: var(--sky);
    text-transform: uppercase;
    letter-spacing: 1px;
  }
  .front__brand { right: 26px; bottom: 26px; }

  .services {
    position: absolute;
    left: 58px;
    top: 72px;
    width: 430px;
  }
  .services__mark {
    position: absolute;
    right: 60px;
    top: -36px;
    width: 48px;
    height: 48px;
    background: var(--blue);
  }
  .services__title {
    font-size: 22px;
    color: var(--navy);
    letter-spacing: 1px;
    margin-bottom: 14px;
    font-weight: 400;
  }
  .services__list {
    list-style: none;
    font-size: 11.5px;
    line-height: 1.7;
    color: var(--sky);
  }
</style>
</head>
<body>

  <section class="card card--front" aria-label="Business card front">
    <svg class="card__stripes" width="540" height="309" viewBox="0 0 540 309" aria-hidden="true">
      <!-- top band, deeper on the left -->
      <polygon points="0,0 540,0 540,22 230,22 212,40 0,40" fill="var(--band-grey)"/>
      <polyline points="0,46 214,46 232,28 540,28" fill="none" stroke="var(--line-white)" stroke-width="3"/>
      <polyline points="0,52 216,52 234,34 540,34" fill="none" stroke="var(--line-grey)" stroke-width="2"/>
      <!-- bottom band, deeper on the right -->
      <polygon points="0,276 290,276 320,222 540,222 540,309 0,309" fill="var(--band-grey)"/>
      <polyline points="0,270 286,270 316,216 540,216" fill="none" stroke="var(--line-white)" stroke-width="3"/>
      <polyline points="0,264 282,264 312,210 540,210" fill="none" stroke="var(--line-grey)" stroke-width="2"/>
    </svg>
    <p class="front__email">Fenwarcoatings.utah@brelmox.com</p>
    <div class="front__identity">
      <h1 class="front__name">Rodrigo Fenwar</h1>
      <p class="front__phone">801-437-2190</p>
    </div>
    <div class="brand front__brand">
      <span class="brand__mark" aria-hidden="true"></span>
      <span class="brand__name">Fenwar<br>Coatings</span>
    </div>
  </section>

  <section class="card card--back" aria-label="Business card back">
    <div class="services">
      <span class="services__mark" aria-hidden="true"></span>
      <h2 class="services__title">SERVICES OFFERED:</h2>
      <ul class="services__list">
        <li>Custom Paint &amp; Stain • Interior &amp;</li>
        <li>Exterior • Epoxy Coatings/Garage</li>
        <li>Floors • Cabinet Refinishing • Log</li>
        <li>Staining &amp; Refinishing</li>
      </ul>
    </div>
  </section>

</body>
</html>
```